Brevard Trade Partners - we are Asian sourcing agents

We are sourcing agents based in the USA and we act as sourcing agents for clients in throughout the world. We focus primarily on custom sewn goods. So basically companies who do not have the in-house expertise to do it themselves, come to us and have us find suitable factories in Asia to do the production. We are middlemen. We find the factories...quote the project...manage the quality control and then deliver the goods directly to our customer's door. We pride ourselves in making the communication very easy and precise.

Current page is www.brevardtradepartners.com

I am not happy w/ the overall look. The spacing...the photos, the fonts...the design elements...the pictures. I want a cool, crisp design that conveys professionalism and clearly depicts/explains what we do.

Requirements
Must have
• use my logo....I like it...it was designed by someone on this website.
Nice to have
• a video/animation of the entire process would be wonderful. Showing initial contact with our office in the USA...then to my correspondence with my offices in Taiwan and in Hong Kong...and then back and fort w/ the customer.....and then between my people in Hong Kong/Taiwan with the local factories......and then a quote is generated and sent to my client......to samples being made and sent for approval.....to a PO being generated......to final samples being sent.....to the order being shipped and delivered to the clients warehouse. I was thinking of an animation showing arrows and text showing the back and forth communication and explaining how the process flows.

```html
<!DOCTYPE html>
<html lang="en">
<head>
<meta charset="utf-8">
<title>Brevard Trade Partners – Asian Outsourcing Made Easy</title>
<link rel="stylesheet" href="https://fonts.googleapis.com/css2?family=Roboto:wght@400;500;700;900&display=swap">
<style>
:root{
  --navy:#131a5c;
  --navy-deep:#0f1550;
  --green:#5a7f14;
  --green-text:#5f8a12;
  --ink:#222;
  --body:#444;
  --muted:#8a8f99;
  --grey-band:#ececec;
  --rule:#d6d6d6;
  --white:#fff;
}
*{box-sizing:border-box;margin:0;padding:0}
html,body{width:1200px;height:3309px;overflow:hidden}
body{font-family:"Roboto",Arial,sans-serif;color:var(--ink);background:var(--white);position:relative}
a{color:inherit;text-decoration:none}

/* header */
.site-header{height:147px;position:relative;background:var(--white)}
.brand{position:absolute;left:104px;top:44px;display:flex;align-items:center;gap:12px}
.brand-mark{width:22px;height:22px;border-radius:50%;background:var(--navy)}
.brand-name{font-size:27px;font-weight:900;color:var(--navy);letter-spacing:.2px;line-height:1}
.main-nav{position:absolute;right:104px;top:54px;display:flex;align-items:center;gap:42px}
.main-nav a{font-size:14px;font-weight:500;color:#111;text-transform:uppercase}
.main-nav .nav-cta{background:var(--green);color:var(--white);padding:14px 24px;font-weight:700}

/* hero */
.hero{height:618px;position:relative;background:linear-gradient(180deg,#3f5f88 0%,#8d8fa0 30%,#c58a55 52%,#6a4a30 72%,#3a281b 100%)}
.hero-dots{position:absolute;left:96px;top:413px;display:flex;flex-direction:column;gap:8px}
.hero-dots span{width:16px;height:16px;border-radius:50%;border:2px solid var(--white)}
.hero-dots span.on{background:var(--white)}
.hero-copy{position:absolute;left:145px;top:410px;color:var(--white)}
.hero-copy h1{font-size:37px;font-weight:500;margin-bottom:10px}
.hero-copy p{font-size:22px}

/* section titles */
.section-title{font-size:18px;font-weight:700;color:var(--green-text);text-transform:uppercase;text-align:center}

/* quote */
.quote{height:245px;text-align:center;padding-top:40px}
.quote p{font-size:20px;color:var(--ink);margin-top:22px}
.btn-quote{display:inline-block;margin-top:26px;background:var(--green);color:var(--white);font-size:23px;width:236px;height:63px;line-height:63px}

/* how it works */
.how{height:487px;background:var(--grey-band);padding-top:38px}
.video{position:relative;width:820px;height:355px;margin:32px auto 0;background:linear-gradient(135deg,#2d4f8c 0%,#6b7a8a 45%,#a79c84 70%,#4b4a44 100%);overflow:hidden}
.video-play{position:absolute;left:374px;top:128px;width:72px;height:72px;border-radius:50%;background:rgba(0,0,0,.55)}
.video-bar{position:absolute;left:0;right:0;bottom:0;height:38px;background:#1d1d1d}
.video-progress{position:absolute;left:0;right:0;top:0;height:5px;background:#555}
.video-progress i{position:absolute;left:0;top:0;height:5px;width:405px;background:#d41f1f}
.video-progress b{position:absolute;left:398px;top:-4px;width:13px;height:13px;border-radius:50%;background:#eee}
.video-time{position:absolute;left:100px;top:16px;font-size:11px;color:#ddd}

/* sourcing */
.sourcing{height:503px;padding-top:42px;position:relative}
.sourcing .intro{width:800px;margin:26px auto 0;text-align:center;font-size:15.5px;line-height:31px;color:var(--body)}
.carousel{position:absolute;left:104px;top:221px;width:992px;display:flex;justify-content:space-between}
.carousel-arrow{position:absolute;top:300px}
.carousel-arrow.prev{left:58px}
.carousel-arrow.next{right:58px}
.product{width:236px;text-align:center}
.product-photo{height:203px;border:3px solid #e6e6e6;background:linear-gradient(180deg,#f7f7f7,#e4e4e4)}
.product-name{margin-top:16px;font-size:17px;letter-spacing:2px;color:var(--green-text)}

/* knowledge */
.know{height:647px;background:var(--grey-band);padding-top:44px;position:relative}
.know-grid{position:absolute;left:104px;top:110px;width:992px;display:grid;grid-template-columns:1fr 1fr}
.know-grid::after{content:"";position:absolute;left:496px;top:0;height:510px;border-left:1px solid var(--rule)}
.topic{height:170px;padding:22px 20px 0 66px;position:relative;border-bottom:1px solid var(--rule)}
.topic:nth-child(odd){margin-right:18px}
.topic:nth-child(even){margin-left:18px;padding-left:66px}
.topic:nth-child(n+5){border-bottom:none}
.topic svg{position:absolute;left:0;top:22px}
.topic:nth-child(even) svg{left:8px}
.topic h3{font-size:14.5px;font-weight:700;color:var(--navy);margin-bottom:10px}
.topic p{font-size:13.5px;line-height:24px;color:var(--body);height:48px;overflow:hidden}
.read-more{display:inline-block;margin-top:10px;font-size:11px;font-weight:700;color:var(--green-text);text-transform:uppercase}

/* footer */
.footer-links{height:500px;background:var(--navy-deep);position:relative;color:var(--white)}
.footer-col{position:absolute;top:38px}
.footer-col h4{font-size:13px;font-weight:700;text-transform:uppercase;margin-bottom:24px}
.footer-col li{list-style:none;font-size:12.5px;line-height:34px}
.footer-col .group+.group{margin-top:30px}
.footer-divider{position:absolute;top:44px;height:410px;border-left:1px solid rgba(255,255,255,.12)}
.footer-base{height:162px;background:var(--navy-deep);border-top:1px solid rgba(255,255,255,.12);position:relative;color:var(--white)}
.footer-brand{position:absolute;left:104px;top:26px;display:flex;align-items:center;gap:10px}
.footer-brand .brand-mark{background:var(--white);width:40px;height:40px}
.footer-brand .brand-name{color:var(--white);font-size:20px}
.footer-address{position:absolute;left:104px;top:104px;font-size:12px;line-height:26px}
.social{position:absolute;right:104px;top:32px;text-align:right;font-size:12px}
.social-icons{display:flex;gap:14px;justify-content:flex-end;margin-top:14px}
.social-icons span{width:14px;height:14px;border-radius:50%;background:var(--white)}
</style>
</head>
<body>

<header class="site-header">
  <a class="brand" href="#"><span class="brand-mark"></span><span class="brand-name">Brevard Trade Partners</span></a>
  <nav class="main-nav">
    <a href="#">Home</a>
    <a href="#">About Us</a>
    <a href="#">Product Categories</a>
    <a class="nav-cta" href="#">Request Quote</a>
  </nav>
</header>

<section class="hero" role="img" aria-label="Photo of the Great Wall of China at sunset">
  <div class="hero-dots"><span class="on"></span><span></span><span class="on"></span><span class="on"></span></div>
  <div class="hero-copy">
    <h1>Asian Outsourcing Made Easy!</h1>
    <p>Custom Sewn Goods Made to Your Specifications</p>
  </div>
</section>

<section class="quote">
  <h2 class="section-title">Request a Quote</h2>
  <p>Please contact us for immediate consultation regarding your outsourcing project.</p>
  <a class="btn-quote" href="#">Request Quote</a>
</section>

<section class="how">
  <h2 class="section-title">How It Works</h2>
  <div class="video" role="img" aria-label="Video still of a factory worker at an industrial sewing machine">
    <div class="video-play"><svg width="72" height="72" viewBox="0 0 72 72"><path d="M29 22 L52 36 L29 50 Z" fill="#fff"/></svg></div>
    <div class="video-bar">
      <div class="video-progress"><i></i><b></b></div>
      <svg style="position:absolute;left:16px;top:15px" width="60" height="14" viewBox="0 0 60 14"><path d="M0 1 L10 7 L0 13Z" fill="#ddd"/><path d="M34 4h4l5-4v14l-5-4h-4z" fill="#ddd"/></svg>
      <span class="video-time">0:58 / 5:13</span>
    </div>
  </div>
</section>

<section class="sourcing">
  <h2 class="section-title">Sourcing Custom Goods in China</h2>
  <p class="intro">We outsource sewing services direct from China. Our long-established and extensive network of offshore factory-partners provides our clients with access to a wide variety of contract sewing expertise from Chinese manufacturers. Clients only need to communicate with our US agents.</p>
  <svg class="carousel-arrow prev" width="16" height="28" viewBox="0 0 16 28"><path d="M13 2 L3 14 L13 26" fill="none" stroke="#999" stroke-width="2.5"/></svg>
  <svg class="carousel-arrow next" width="16" height="28" viewBox="0 0 16 28"><path d="M3 2 L13 14 L3 26" fill="none" stroke="#999" stroke-width="2.5"/></svg>
  <div class="carousel">
    <div class="product"><div class="product-photo" role="img" aria-label="Photo of a messenger bag"></div><div class="product-name">Bags</div></div>
    <div class="product"><div class="product-photo" role="img" aria-label="Photo of a pair of ski gloves"></div><div class="product-name">Gloves</div></div>
    <div class="product"><div class="product-photo" role="img" aria-label="Photo of a covered motorcycle"></div><div class="product-name">Covers</div></div>
    <div class="product"><div class="product-photo" role="img" aria-label="Photo of colourful phone cases"></div><div class="product-name">Cases</div></div>
  </div>
</section>

<section class="know">
  <h2 class="section-title">What You Need to Know</h2>
  <div class="know-grid">
    <article class="topic">
      <svg width="34" height="22" viewBox="0 0 34 22"><path d="M2 8 L10 3 L17 6 L24 3 L32 8 L24 17 L18 20 L10 14 Z" fill="var(--navy)"/></svg>
      <h3>Contract Sewing in China</h3>
      <p>Despite recent wage increases earned by China factory workers, and the rise of the Yuan versus the Dollar...</p>
      <a class="read-more" href="#">Read More ▸</a>
    </article>
    <article class="topic">
      <svg width="22" height="22" viewBox="0 0 22 22"><path d="M4 9 A7 7 0 0 1 17 6" fill="none" stroke="var(--navy)" stroke-width="3"/><path d="M14 3h6v6z" fill="var(--navy)"/><path d="M18 13 A7 7 0 0 1 5 16" fill="none" stroke="var(--navy)" stroke-width="3"/><path d="M8 19H2v-6z" fill="var(--navy)"/></svg>
      <h3>What is the Process?</h3>
      <p>Our aim at Brevard Trade Partners is to make the entire importing process as easy as possible for our clients.</p>
      <a class="read-more" href="#">Read More ▸</a>
    </article>
    <article class="topic">
      <svg width="24" height="24" viewBox="0 0 24 24"><rect x="2" y="5" width="16" height="16" fill="none" stroke="var(--navy)" stroke-width="2.5"/><path d="M9 15 L20 4 L23 7 L12 18 L8 19Z" fill="var(--navy)"/></svg>
      <h3>What the Minimum Order?</h3>
      <p>That's a question I hear at least several times a week, and there's no definitive answer to that question.</p>
      <a class="read-more" href="#">Read More ▸</a>
    </article>
    <article class="topic">
      <svg width="20" height="24" viewBox="0 0 20 24"><text x="4" y="19" font-family="Roboto,Arial,sans-serif" font-weight="900" font-size="20" fill="var(--navy)">?</text></svg>
      <h3>Contract Outsourcing FAQ</h3>
      <p>Despite having higher labor costs than some other Asian countries, China remains the best overall choice after all</p>
      <a class="read-more" href="#">Read More ▸</a>
    </article>
    <article class="topic">
      <svg width="24" height="24" viewBox="0 0 24 24"><path d="M17 2 L22 7 L9 20 L3 22 L4 15 Z" fill="var(--navy)"/></svg>
      <h3>Outsourcing Case Study</h3>
      <p>A potential client contacted Brevard Trade Partners to see if we might make the entire process of outsourcing</p>
      <a class="read-more" href="#">Read More ▸</a>
    </article>
    <article class="topic">
      <svg width="24" height="24" viewBox="0 0 24 24"><circle cx="12" cy="12" r="7" fill="none" stroke="var(--navy)" stroke-width="5" stroke-dasharray="3.5 2"/><circle cx="12" cy="12" r="5.5" fill="var(--navy)"/><circle cx="12" cy="12" r="2.2" fill="var(--grey-band)"/></svg>
      <h3>Custom Industrial Sewing in China</h3>
      <p>One of the most heard requests we get are from companies/persons inquiring about our industrial sewing</p>
      <a class="read-more" href="#">Read More ▸</a>
    </article>
  </div>
</section>

<footer>
  <div class="footer-links">
    <div class="footer-col" style="left:104px">
      <h4>Bags</h4>
      <ul><li>Athletic Bags</li><li>Backpacks</li><li>Computer Bags</li><li>Cooler Bags</li><li>Cosmetic Bags</li><li>Handbags</li><li>Messenger Bags</li><li>Shopping Bags</li><li>Tool Bags</li><li>Travel Bags</li><li>Yoga Bags</li></ul>
    </div>
    <div class="footer-divider" style="left:263px"></div>
    <div class="footer-col" style="left:323px">
      <h4>Covers</h4>
      <ul><li>ATV Covers</li><li>Chair Covers</li><li>Equipment Covers</li><li>Golf Cart Covers</li><li>Motorcycle Covers</li><li>Outdoor Furniture Covers</li><li>Outdoor Grill Cover</li><li>Personal Watercraft Covers</li><li>Snowmobile Covers</li></ul>
    </div>
    <div class="footer-divider" style="left:553px"></div>
    <div class="footer-col" style="left:617px">
      <div class="group"><h4>Cases</h4>
      <ul><li>Cosmetic Cases</li><li>Phone Cases</li><li>Tool Bags and Tool Cases</li></ul></div>
      <div class="group" style="margin-top:40px"><h4>Gloves</h4>
      <ul><li>Batting Gloves</li><li>Garden Gloves</li><li>Mechanic Gloves</li><li>Safety Gloves</li><li>Ski Gloves</li></ul></div>
    </div>
    <div class="footer-divider" style="left:826px"></div>
    <div class="footer-col" style="left:886px">
      <div class="group"><h4>Medical Accessories</h4>
      <ul><li>Medical Equipment Covers</li><li>Medical Pads</li><li>Medical Sheets &amp; Bedding Supplies</li><li>Oxygen Tank Cases and Bags</li></ul></div>
      <div class="group"><h4>Sewn Goods</h4>
      <ul><li>Pet Collars, Leashes, &amp; Harnesses</li><li>Socks</li></ul></div>
      <div class="group"><h4>Sporting Goods</h4>
      <ul><li>Yoga Mats</li><li>Yoga Gear and Accessories</li></ul></div>
    </div>
  </div>
  <div class="footer-base">
    <div class="footer-brand"><span class="brand-mark"></span><span class="brand-name">Brevard Trade Partners</span></div>
    <div class="footer-address">
      Brevard Trade Partners, LLC &nbsp;|&nbsp; 48 Harbor Street &nbsp;|&nbsp; Suite B-4 &nbsp;|&nbsp; Dover, NH 03820<br>
      © Brevard Trade Partners, LLC. | USA - Hong Kong - Taipei
    </div>
    <div class="social">
      Connect With Us
      <div class="social-icons"><span></span><span></span><span></span><span></span></div>
    </div>
  </div>
</footer>

</body>
</html>
```